LHP Regal Business Card Design 2020

Your Manor Steward is looking for a business card that is clean and straight to the point but still looks high-end and attractive. We are a team comprised of management and field professionals focused on the high-end residential marketplace. We serve homeowners and trade professionals directly based out of the Metrowest/Boston area. We provide client services as well as construction/renovation services.
We are aiming for a black and white feel (white background and black text) and a matte finish with rounded edges.

We want to emphasis our vision of "Properties - Projects - Partners".
Dana Pellham is the president of LHP

Please include the following areas we service: Boston/Cape/Newport
Please make sure to include Dana's mobile (555) 213 4480 & office number (555) 640 1937, email dana@yourmanorsteward.example and website www.yourmanorsteward.example

Colors

Designer to choose only greyscale colors for use in the design.

Requirements
Must have
• Include "Properties - Projects - Partners" in design

Include "After Hours Emergency Support # 1800 555 0142" with icon

```html
<!DOCTYPE html>
<html lang="en">
<head>
<meta charset="utf-8">
<title>LHP Business Cards</title>
<link href="https://fonts.googleapis.com/css2?family=Nunito+Sans:wght@400;600;800;900&display=swap" rel="stylesheet">
<style>
:root{
  --board:#c4d3d0;
  --ink:#222426;
  --paper:#ffffff;
  --band:#222426;
  --band-end:#5e6062;
  --front:#232425;
  --front-mark:#3a3b3d;
  --muted:#cfd2d3;
}
*{box-sizing:border-box;margin:0;padding:0}
html,body{width:801px;height:1200px;overflow:hidden}
body{background:var(--board);font-family:"Nunito Sans",Arial,sans-serif;color:var(--ink);position:relative}
.card{position:absolute;width:339px;height:194px;border-radius:12px;overflow:hidden;background:var(--paper);box-shadow:2px 3px 5px rgba(0,0,0,.28)}
.card-front{left:232px;top:53px;background:var(--front)}
.front-mark{position:absolute;left:0;right:0;top:52px;text-align:center;font-weight:900;font-size:74px;line-height:1;color:var(--front-mark);letter-spacing:-2px}
.vision{position:absolute;left:0;right:0;top:167px;text-align:center;color:var(--muted);font-size:8px;letter-spacing:1.6px}
.col-l{left:40px}.col-r{left:422px}
.row1{top:277px}.row2{top:499px}.row3{top:725px}.row4{top:951px}
.brand{position:absolute;left:21px;top:18px;width:106px;text-align:center}
.brand-mark{font-weight:900;font-size:44px;line-height:1;letter-spacing:-1px;color:var(--ink)}
.brand-name{font-weight:900;font-size:6.6px;letter-spacing:.9px;margin-top:3px;white-space:nowrap}
.brand.centered{left:0;right:0;width:auto;top:24px}
.brand.centered .brand-mark{font-size:56px}
.brand.centered .brand-name{font-size:8.6px;letter-spacing:1.3px}
.person{position:absolute;right:22px;top:83px;text-align:right}
.person-name{font-weight:900;font-size:12px;line-height:1.1;letter-spacing:.2px}
.person-role{font-size:8.4px;line-height:1.4}
.rule{position:absolute;left:21px;right:21px;top:113px;height:1px;background:var(--ink)}
.contacts{position:absolute;left:21px;bottom:29px;list-style:none;font-size:8.4px;line-height:11.3px}
.contacts li{display:flex;align-items:center;gap:3px;white-space:nowrap}
.contacts svg{width:8px;height:8px;fill:var(--ink);flex:none}
.areas{position:absolute;right:22px;bottom:29px;font-size:8.4px;line-height:11.3px;word-spacing:1px}
.band{position:absolute;left:0;right:0;bottom:0;height:19px;background:linear-gradient(90deg,var(--band) 0 84%,var(--band-end) 92%);display:flex;align-items:center;justify-content:space-between;padding:0 22px 0 21px}
.band-site{color:var(--muted);font-size:8.2px;letter-spacing:1px}
.band-mark{color:#fff;font-weight:900;font-size:17px;line-height:1;letter-spacing:-.5px}
</style>
</head>
<body>
<svg width="0" height="0" style="position:absolute" aria-hidden="true">
  <symbol id="i-mobile" viewBox="0 0 10 10"><path d="M3 0h4a1 1 0 0 1 1 1v8a1 1 0 0 1-1 1H3a1 1 0 0 1-1-1V1a1 1 0 0 1 1-1zm0 1.2v6.6h4V1.2z"/></symbol>
  <symbol id="i-phone" viewBox="0 0 10 10"><path d="M2 .5l1.6 2.2-1 1a6 6 0 0 0 3.7 3.7l1-1L9.5 8 8.3 9.5C4.3 9.3.7 5.7.5 1.7z"/></symbol>
  <symbol id="i-alarm" viewBox="0 0 10 10"><path d="M3 5a2 2 0 0 1 4 0v2.5H3zM1.5 8h7v1.5h-7zM4.7 0h.6v1.6h-.6zM1 1.3l.5-.4 1 1.2-.5.4zM9 1.3l-.5-.4-1 1.2.5.4zM0 4h1.5v.6H0zM8.5 4H10v.6H8.5z"/></symbol>
  <symbol id="i-mail" viewBox="0 0 10 10"><path d="M.5 2h9v6.5h-9zm1.2 1l3.3 2.6L8.3 3zm-.2 1v3.5h7V4L5 6.7z"/></symbol>
</svg>

<section class="card card-front">
  <div class="front-mark">LHP</div>
  <p class="vision">PROPERTIES - PROJECTS - PARTNERS</p>
</section>

<section class="card col-l row1">
  <div class="brand"><div class="brand-mark">LHP</div><div class="brand-name">YOUR MANOR STEWARD</div></div>
  <div class="person"><div class="person-name">GLEN MARLOW</div><div class="person-role">Vice President</div></div>
  <div class="rule"></div>
  <ul class="contacts">
    <li><svg><use href="#i-mobile"/></svg>(555) 318 2207</li>
    <li><svg><use href="#i-phone"/></svg>(555) 640 1937</li>
    <li><svg><use href="#i-alarm"/></svg>(800) 555 0142</li>
    <li><svg><use href="#i-mail"/></svg>glen@yourmanorsteward.example</li>
  </ul>
  <div class="areas">BOSTON | CAPE | NEWPORT</div>
  <div class="band"><span class="band-site">yourmanorsteward.example</span><span class="band-mark">LHP</span></div>
</section>

<section class="card col-r row1">
  <div class="brand"><div class="brand-mark">LHP</div><div class="brand-name">YOUR MANOR STEWARD</div></div>
  <div class="person"><div class="person-name">DANA PELLHAM</div><div class="person-role">President</div></div>
  <div class="rule"></div>
  <ul class="contacts">
    <li><svg><use href="#i-mobile"/></svg>(555) 213 4480</li>
    <li><svg><use href="#i-phone"/></svg>(555) 640 1937</li>
    <li><svg><use href="#i-alarm"/></svg>(800) 555 0142</li>
    <li><svg><use href="#i-mail"/></svg>dana@yourmanorsteward.example</li>
  </ul>
  <div class="areas">BOSTON | CAPE | NEWPORT</div>
  <div class="band"><span class="band-site">yourmanorsteward.example</span><span class="band-mark">LHP</span></div>
</section>

<section class="card col-l row2">
  <div class="brand"><div class="brand-mark">LHP</div><div class="brand-name">YOUR MANOR STEWARD</div></div>
  <div class="person"><div class="person-name">OWEN PRUITT</div><div class="person-role">Project Supervisor</div></div>
  <div class="rule"></div>
  <ul class="contacts">
    <li><svg><use href="#i-mobile"/></svg>(555) 472 9015</li>
    <li><svg><use href="#i-phone"/></svg>(555) 640 1937</li>
    <li><svg><use href="#i-alarm"/></svg>(800) 555 0142</li>
    <li><svg><use href="#i-mail"/></svg>office@yourmanorsteward.example</li>
  </ul>
  <div class="areas">BOSTON | CAPE | NEWPORT</div>
  <div class="band"><span class="band-site">yourmanorsteward.example</span><span class="band-mark">LHP</span></div>
</section>

<section class="card col-r row2">
  <div class="brand"><div class="brand-mark">LHP</div><div class="brand-name">YOUR MANOR STEWARD</div></div>
  <div class="person"><div class="person-name">LUCA BENEDETTI</div><div class="person-role">Client Services</div></div>
  <div class="rule"></div>
  <ul class="contacts">
    <li><svg><use href="#i-mobile"/></svg>(555) 806 3321</li>
    <li><svg><use href="#i-phone"/></svg>(555) 640 1937</li>
    <li><svg><use href="#i-alarm"/></svg>(800) 555 0142</li>
    <li><svg><use href="#i-mail"/></svg>luca@yourmanorsteward.example</li>
  </ul>
  <div class="areas">BOSTON | CAPE | NEWPORT</div>
  <div class="band"><span class="band-site">yourmanorsteward.example</span><span class="band-mark">LHP</span></div>
</section>

<section class="card col-l row3">
  <div class="brand"><div class="brand-mark">LHP</div><div class="brand-name">YOUR MANOR STEWARD</div></div>
  <div class="person"><div class="person-name">MARA QUINTELA</div><div class="person-role">Client Services</div></div>
  <div class="rule"></div>
  <ul class="contacts">
    <li><svg><use href="#i-mobile"/></svg>(555) 239 6674</li>
    <li><svg><use href="#i-phone"/></svg>(555) 640 1937</li>
    <li><svg><use href="#i-alarm"/></svg>(800) 555 0142</li>
    <li><svg><use href="#i-mail"/></svg>mara@yourmanorsteward.example</li>
  </ul>
  <div class="areas">BOSTON | CAPE | NEWPORT</div>
  <div class="band"><span class="band-site">yourmanorsteward.example</span><span class="band-mark">LHP</span></div>
</section>

<section class="card col-r row3">
  <div class="brand"><div class="brand-mark">LHP</div><div class="brand-name">YOUR MANOR STEWARD</div></div>
  <div class="person"><div class="person-name">BRENT HOLLIS</div><div class="person-role">Project Supervisor</div></div>
  <div class="rule"></div>
  <ul class="contacts">
    <li><svg><use href="#i-mobile"/></svg>(555) 751 4089</li>
    <li><svg><use href="#i-phone"/></svg>(555) 640 1937</li>
    <li><svg><use href="#i-alarm"/></svg>(800) 555 0142</li>
    <li><svg><use href="#i-mail"/></svg>office@yourmanorsteward.example</li>
  </ul>
  <div class="areas">BOSTON | CAPE | NEWPORT</div>
  <div class="band"><span class="band-site">yourmanorsteward.example</span><span class="band-mark">LHP</span></div>
</section>

<section class="card col-l row4">
  <div class="brand centered"><div class="brand-mark">LHP</div><div class="brand-name">YOUR MANOR STEWARD</div></div>
  <div class="rule" style="top:117px"></div>
  <ul class="contacts">
    <li><svg><use href="#i-phone"/></svg>(555) 640 1937</li>
    <li><svg><use href="#i-alarm"/></svg>(800) 555 0142</li>
    <li><svg><use href="#i-mail"/></svg>office@yourmanorsteward.example</li>
  </ul>
  <div class="areas">BOSTON | CAPE | NEWPORT</div>
  <div class="band"><span class="band-site">yourmanorsteward.example</span><span class="band-mark">LHP</span></div>
</section>

<section class="card col-r row4">
  <div class="brand"><div class="brand-mark">LHP</div><div class="brand-name">YOUR MANOR STEWARD</div></div>
  <div class="person"><div class="person-name">NEIL CORRAN</div><div class="person-role">Field Supervisor</div></div>
  <div class="rule"></div>
  <ul class="contacts">
    <li><svg><use href="#i-mobile"/></svg>(555) 964 1253</li>
    <li><svg><use href="#i-phone"/></svg>(555) 640 1937</li>
    <li><svg><use href="#i-alarm"/></svg>(800) 555 0142</li>
    <li><svg><use href="#i-mail"/></svg>neil@yourmanorsteward.example</li>
  </ul>
  <div class="areas">BOSTON | CAPE | NEWPORT</div>
  <div class="band"><span class="band-site">yourmanorsteward.example</span><span class="band-mark">LHP</span></div>
</section>
</body>
</html>
```